Law Offices business card

Hi there, I'll need business card for the Law Offices of Colin Matheny. The information must convey his strategic approach and quick resolution to complex business litigation needs. Please emphasize Civil Litigation, Corporate Law, Business Governance and Real Estate Law. Colin has over 25 years of experience in these fields.The card should be modern and edgy and the message should be clear. Please consult his current website for ideas.

```html
<!DOCTYPE html>
<html lang="en">
<head>
<meta charset="utf-8">
<title>Law Offices of Colin Matheny – Business Card</title>
<link href="https://fonts.googleapis.com/css2?family=Cinzel:wght@400;500&family=Source+Sans+3:wght@400;600;700&display=swap" rel="stylesheet">
<style>
  :root {
    --bg-top: #2b2b2b;
    --bg-bottom: #050505;
    --card: #ffffff;
    --accent: #e2701f;
    --ink: #111111;
    --muted: #222222;
  }
  * { margin: 0; padding: 0; box-sizing: border-box; }
  html, body { width: 1200px; height: 900px; overflow: hidden; }
  body {
    background: linear-gradient(180deg, var(--bg-top) 0%, var(--bg-bottom) 100%);
    font-family: "Source Sans 3", Arial, sans-serif;
    position: relative;
  }
  .card {
    position: absolute;
    top: 306px;
    width: 440px;
    height: 271px;
    background: var(--card);
    border-radius: 10px;
  }
  .card--front { left: 149px; }
  .card--back { left: 608px; }

  /* Front */
  .brand {
    position: absolute;
    left: 22px;
    top: 62px;
    width: 190px;
    text-align: center;
  }
  .brand__mark {
    display: block;
    width: 80px;
    height: 80px;
    margin: 0 auto 18px;
    border-radius: 50%;
    background: var(--accent);
  }
  .brand__name {
    font-family: "Cinzel", "Times New Roman", serif;
    color: var(--ink);
    font-weight: 400;
    line-height: 1.15;
  }
  .brand__line1 { display: block; font-size: 22px; letter-spacing: 1px; }
  .brand__line2 { display: block; font-size: 15px; }

  .details {
    position: absolute;
    left: 230px;
    top: 58px;
    color: var(--muted);
  }
  .details__name {
    color: var(--accent);
    font-weight: 600;
    font-size: 17px;
    line-height: 1;
  }
  .details__title { font-size: 12.5px; margin-top: 4px; }
  .details__address { font-size: 12.5px; line-height: 16px; margin-top: 13px; }
  .contact-list { list-style: none; margin-top: 11px; }
  .contact-list li {
    font-size: 12.5px;
    line-height: 18px;
    display: flex;
    align-items: center;
  }
  .contact-list svg { width: 9px; height: 9px; margin: 0 9px 0 1px; fill: var(--accent); }

  /* Back */
  .back-title {
    position: absolute;
    left: 0; right: 0;
    top: 68px;
    text-align: center;
    font-family: "Cinzel", "Times New Roman", serif;
    color: var(--ink);
    line-height: 1.1;
  }
  .back-title__line1 { display: block; font-size: 38px; letter-spacing: 3px; }
  .back-title__line2 { display: block; font-size: 25px; margin-top: 4px; }
  .services {
    position: absolute;
    left: 0; right: 0;
    top: 201px;
    text-align: center;
    font-size: 14px;
    font-weight: 600;
    color: var(--ink);
  }
</style>
</head>
<body>
  <section class="card card--front">
    <div class="brand">
      <span class="brand__mark"></span>
      <div class="brand__name">
        <span class="brand__line1">Law Offices</span>
        <span class="brand__line2">Of Colin Matheny</span>
      </div>
    </div>
    <div class="details">
      <p class="details__name">Colin Matheny</p>
      <p class="details__title">Attorney</p>
      <p class="details__address">118B Harbor Lane<br>Coral Bay, Florida 33012</p>
      <ul class="contact-list">
        <li><svg viewBox="0 0 10 10"><path d="M2 0.5l1.6 2-1 1.2c.6 1.3 1.4 2.1 2.7 2.7l1.2-1 2 1.6-.9 1.9C4.6 8.7 1.3 5.4.1 1.4z"/></svg>555-204-3186</li>
        <li><svg viewBox="0 0 10 10"><path d="M2.5 0h4.5v3H2.5zM0 3.5h10v5H0zM2 5h1.5v1.2H2zM4.3 5h1.5v1.2H4.3zM6.6 5H8v1.2H6.6z"/></svg>555-204-3187</li>
        <li><svg viewBox="0 0 10 10"><path d="M0 2h10v.8L5 6 0 2.8zM0 3.8l5 3.2 5-3.2V8H0z"/></svg>colin@mathenylaw.com</li>
        <li><svg viewBox="0 0 10 10"><circle cx="5" cy="5" r="4.6"/></svg>www.mathenylaw.com</li>
      </ul>
    </div>
  </section>

  <section class="card card--back">
    <h1 class="back-title">
      <span class="back-title__line1">Law Offices</span>
      <span class="back-title__line2">Of Colin Matheny</span>
    </h1>
    <p class="services">Business Litigation | Real Estate | Title and Closing Services</p>
  </section>
</body>
</html>
```